Website design for an Italian restaurant in Amsterdam

I need a design for a client of mine. It is for Teatro Lucerna, an Italian restaurant in Amsterdam.
We are going for a clean, modern look but we also need to realise an authentic feel.
The restaurant is located in an old movie theatre, that is where the name Teatro Lucerna comes from.
Industry/Entity Type
Italian Restaurant
Number of Pages Required
1 page
Font styles to use
Sans Serif
Colors
Designer to choose colors to be used in the design.

```html
<!DOCTYPE html>
<html lang="en">
<head>
<meta charset="utf-8">
<title>Teatro Lucerna – Italian Restaurant Amsterdam</title>
<link href="https://fonts.googleapis.com/css2?family=Great+Vibes&family=Playfair+Display:wght@400;700&family=Roboto:wght@300;400;500;700&display=swap" rel="stylesheet">
<style>
:root{
  --brand-red:#c0392b;
  --brown:#a88a66;
  --brown-dark:#8a6f50;
  --brown-deep:#6f583f;
  --gold:#e3b23c;
  --ink:#333333;
  --muted:#8a8a8a;
  --line:#dddddd;
  --paper:#ffffff;
  --grey-bg:#f3f3f3;
  --sand:#efe7dd;
}
*{box-sizing:border-box;margin:0;padding:0}
html,body{width:1200px;height:3100px;overflow:hidden}
body{position:relative;background:var(--paper);font-family:'Roboto',sans-serif;color:var(--ink)}
.abs{position:absolute}

/* nav */
.site-nav{position:absolute;top:0;left:0;width:1200px;height:60px;background:var(--paper);box-shadow:0 1px 4px rgba(0,0,0,.08);z-index:5}
.site-nav a{position:absolute;top:0;height:60px;line-height:60px;font-size:11px;font-weight:500;letter-spacing:.5px;color:#666;text-decoration:none;text-transform:uppercase;padding:0 16px}
.site-nav a.active{background:#ececec;color:#333}
.brand{position:absolute;left:450px;top:6px;width:300px;text-align:center}
.brand-name{display:inline-flex;align-items:center;gap:8px;font-family:'Playfair Display',serif;font-size:20px;font-weight:700;color:var(--brand-red);letter-spacing:1px;text-transform:uppercase}
.brand-dot{width:14px;height:14px;border-radius:50%;background:var(--brand-red)}
.brand-sub{font-size:9px;color:var(--muted);letter-spacing:2px;text-transform:uppercase;margin-top:2px}

/* hero */
.hero-photo{position:absolute;top:60px;left:0;width:1200px;height:532px;background:radial-gradient(ellipse at 70% 40%,#d89a4a 0%,#8a5628 35%,#3d2412 80%)}
.hero-text{position:absolute;top:250px;left:0;width:1200px;text-align:center;color:#fff}
.hero-welcome{font-family:'Great Vibes',cursive;font-size:72px;line-height:1}
.hero-title{font-family:'Playfair Display',serif;font-size:54px;letter-spacing:3px;text-transform:uppercase;margin-top:4px}
.hero-sub{font-size:13px;letter-spacing:1px;opacity:.9;margin-top:8px}

/* reservation */
.reserve-bar{position:absolute;top:592px;left:0;width:1200px;height:68px;background:var(--brown)}
.reserve-label{position:absolute;left:170px;top:0;width:120px;height:68px;background:var(--brown-dark);color:#fff;padding:16px 0 0 14px;font-size:17px;font-weight:500;line-height:1.1;text-transform:uppercase}
.reserve-label span{display:block;font-size:11px;font-weight:300}
.field-label{position:absolute;top:25px;color:#fff;font-size:13px}
.field{position:absolute;top:22px;height:24px;background:rgba(255,255,255,.85);border:1px solid #fff;font-size:11px;color:var(--muted);padding:5px 8px}
.btn-gold{position:absolute;background:var(--gold);color:#fff;font-size:11px;font-weight:700;text-transform:uppercase;text-align:center;letter-spacing:.5px}

/* sections */
.section-title{position:absolute;left:0;width:1200px;text-align:center;font-family:'Playfair Display',serif;font-size:24px;letter-spacing:1px;text-transform:uppercase;color:#444}
.special-grid{position:absolute;left:200px;top:828px;width:800px;height:320px;display:grid;grid-template-columns:repeat(4,200px);grid-template-rows:repeat(2,160px);box-shadow:0 2px 10px rgba(0,0,0,.08)}
.dish-photo{width:200px;height:160px}
.dish-text{background:#fff;padding:26px 22px}
.dish-text h3{font-size:12px;font-weight:500;letter-spacing:1px;margin-bottom:10px}
.dish-text p{font-size:10px;line-height:1.6;color:var(--muted)}

.sunday-banner{position:absolute;left:200px;top:1244px;width:800px;height:196px;background:var(--brown);padding:8px}
.sunday-inner{position:relative;width:100%;height:100%;border:2px solid rgba(255,255,255,.8)}
.sunday-head{position:absolute;left:30px;top:28px;color:#fff;font-size:36px;font-weight:300;line-height:1.05;text-transform:uppercase}
.sunday-head strong{font-weight:700;display:block}
.hours{position:absolute;left:30px;top:120px;display:flex;gap:24px;color:#fff;font-size:10px;line-height:1.5}
.sunday-photo{position:absolute;right:0;top:0;width:380px;height:100%;background:linear-gradient(120deg,#3a2a1c,#6b4a2d 50%,#c58e52)}

/* menu */
.menu-section{position:absolute;top:1520px;left:0;width:1200px;height:540px;background:var(--grey-bg)}
.veg-photo{position:absolute;left:0;top:0;width:280px;height:540px;background:linear-gradient(160deg,#c83a2a 0%,#e7b93a 30%,#6a9a3a 55%,#f2eee4 85%)}
.menu-tabs{position:absolute;left:390px;top:168px;width:530px;display:flex;gap:30px;justify-content:flex-start;padding-left:10px;font-size:12px;color:#666}
.menu-tabs span{padding:4px 12px}
.menu-tabs .active{background:#fff;border:1px solid var(--line)}
.menu-cats{position:absolute;left:300px;top:220px;width:200px;list-style:none;font-size:12px;font-weight:500}
.menu-cats li{height:38px;line-height:38px;padding-left:14px;color:#444}
.menu-cats li.active{background:#fff}
.menu-items{position:absolute;left:500px;top:220px;width:440px;background:#fff;padding:10px 20px}
.menu-item{position:relative;height:56px;border-bottom:1px solid #eee;padding-top:10px}
.menu-item:last-child{border-bottom:none}
.menu-item h4{font-size:12px;font-weight:500}
.menu-item p{font-size:10px;color:var(--muted);margin-top:4px}
.menu-item .price{position:absolute;right:0;top:12px;font-size:12px;color:#555}

/* testimonial */
.testimonials{position:absolute;top:2140px;left:0;width:1200px;height:280px;background:var(--sand)}
.avatar{position:absolute;border-radius:50%}
.arrow{position:absolute;width:28px;height:28px;border-radius:50%;background:#fff;border:1px solid #ddd}
.quote{position:absolute;left:380px;top:88px;width:420px}
.quote h5{font-size:13px;font-weight:700}
.quote p{font-size:10px;line-height:1.6;color:#666;margin-top:6px}
.quote .author{font-size:10px;font-weight:500;margin-top:6px;display:flex;align-items:center;gap:10px}
.quote .author i{display:inline-block;width:70px;height:6px;background:var(--gold)}

/* contact */
.contact-title{position:absolute;left:210px;top:2500px;font-family:'Playfair Display',serif;font-size:24px;text-transform:uppercase;color:#444}
.form-field{position:absolute;left:210px;width:390px;border:1px solid var(--line);background:#fafafa;font-size:11px;color:var(--muted);padding:8px 10px}
.social-widget{position:absolute;left:732px;top:2496px;width:248px;height:300px;border:1px solid var(--line);background:#fff}
.widget-photo{height:170px;background:linear-gradient(180deg,#4a5a6a,#8a7060 60%,#3a3a3a)}
.widget-body{padding:10px;font-size:11px}
.widget-body strong{display:block;font-size:12px}
.widget-body span{color:var(--muted);font-size:10px}
.widget-lines i{display:block;height:6px;background:#eee;margin-top:8px}

/* footer */
.site-footer{position:absolute;top:2872px;left:0;width:1200px;height:228px;background:var(--brown)}
.foot-brand{position:absolute;left:210px;top:50px;color:#fff}
.foot-brand .name{display:flex;align-items:center;gap:8px;font-family:'Playfair Display',serif;font-size:20px;font-weight:700;letter-spacing:1px;text-transform:uppercase}
.foot-brand .name i{width:14px;height:14px;border-radius:50%;background:#fff}
.foot-brand .sub{font-size:9px;letter-spacing:2px;text-transform:uppercase;opacity:.85;margin-top:2px}
.foot-brand address{font-style:normal;font-size:11px;line-height:1.6;margin-top:14px}
.foot-nav{position:absolute;left:720px;top:112px;display:flex;gap:20px;font-size:11px;color:#fff}
.foot-social{position:absolute;left:920px;top:80px;display:flex;gap:12px}
.foot-social i{width:16px;height:16px;border-radius:50%;background:#fff}
.copyright{position:absolute;left:0;bottom:0;width:1200px;height:32px;line-height:32px;background:var(--brown-deep);color:#e9dfd2;font-size:10px;text-align:center}
</style>
</head>
<body>

<nav class="site-nav">
  <a class="active" style="left:200px">Home</a>
  <a style="left:262px">Menu</a>
  <a style="left:322px">Group Menu</a>
  <div class="brand">
    <div class="brand-name"><span class="brand-dot"></span>Teatro Lucerna</div>
    <div class="brand-sub">Ristorante italiano</div>
  </div>
  <a style="left:780px">Reservation</a>
  <a style="left:870px">Contact</a>
  <a style="left:940px">Blog</a>
</nav>

<div class="hero-photo" role="img" aria-label="Warmly lit restaurant interior with dining tables and open kitchen"></div>
<div class="hero-text">
  <div class="hero-welcome">Welcome to</div>
  <div class="hero-title">Teatro Lucerna</div>
  <div class="hero-sub">The finest Italian cuisine in the heart of Amsterdam</div>
</div>

<div class="reserve-bar">
  <div class="reserve-label">Reserve<span>your table</span></div>
  <div class="field-label" style="left:332px">Guests:</div>
  <div class="field" style="left:380px;width:150px">nr. of guests</div>
  <div class="field-label" style="left:570px">When:</div>
  <div class="field" style="left:612px;width:170px">select date
    <svg class="abs" style="right:6px;top:5px" width="12" height="12" viewBox="0 0 12 12"><rect x="1" y="2" width="10" height="9" fill="none" stroke="#999"/><line x1="1" y1="5" x2="11" y2="5" stroke="#999"/></svg>
  </div>
  <div class="btn-gold" style="left:922px;top:22px;width:92px;height:24px;line-height:24px">Reserve</div>
</div>

<h2 class="section-title" style="top:724px">Monthly Special</h2>
<div class="special-grid">
  <div class="dish-photo" role="img" aria-label="Plate of tagliatelle with sauce" style="background:linear-gradient(135deg,#e0b070,#b86a2e)"></div>
  <div class="dish-text"><h3>LOREM IPSUM</h3><p>Lorem ipsum dolor sit amet, consectetur adipiscing elit sed do.</p></div>
  <div class="dish-photo" role="img" aria-label="Spaghetti with tomato sauce" style="background:linear-gradient(135deg,#d5502e,#8a2a1a)"></div>
  <div class="dish-text"><h3>LOREM IPSUM</h3><p>Lorem ipsum dolor sit amet, consectetur adipiscing elit sed do.</p></div>
  <div class="dish-text"><h3>LOREM IPSUM</h3><p>Lorem ipsum dolor sit amet, consectetur adipiscing elit sed do.</p></div>
  <div class="dish-photo" role="img" aria-label="Fresh salad with tomatoes" style="background:linear-gradient(135deg,#7aa04a,#c8423a)"></div>
  <div class="dish-text"><h3>LOREM IPSUM</h3><p>Lorem ipsum dolor sit amet, consectetur adipiscing elit sed do.</p></div>
  <div class="dish-photo" role="img" aria-label="Pasta dish with meat sauce" style="background:linear-gradient(135deg,#e0a050,#a0482a)"></div>
</div>

<div class="sunday-banner">
  <div class="sunday-inner">
    <div class="sunday-head">Now we're open on<strong>Sundays</strong></div>
    <div class="hours">
      <div>Tue - Sun<br>Lunch</div>
      <div>12:00 - 15:00<br>Dinner</div>
      <div>17:00 - 23:00<br>Daily</div>
    </div>
    <div class="sunday-photo" role="img" aria-label="Chef plating a dish in the kitchen"></div>
    <div class="btn-gold" style="left:300px;top:84px;width:130px;height:28px;line-height:28px">Reserve a table</div>
  </div>
</div>

<section class="menu-section">
  <div class="veg-photo" role="img" aria-label="Fresh vegetables and dry pasta on a white table"></div>
  <h2 class="section-title" style="top:64px;font-size:22px">Menu</h2>
  <div class="menu-tabs"><span class="active">Foods</span><span>Beverages</span><span>Wines</span><span>Deserts</span></div>
  <ul class="menu-cats">
    <li>Le Insalate</li><li class="active">Antipasti</li><li>Le Paste</li><li>Il Pesce</li><li>La Carne</li><li>Dolcini</li><li>Extra</li>
  </ul>
  <div class="menu-items">
    <div class="menu-item"><h4>Pane Burro e Tapenade</h4><p>Fresh bread with butter and olives</p><span class="price">€ 6,50</span></div>
    <div class="menu-item"><h4>Carpaccio di Manzo</h4><p>Thin beef with rocket and parmesan</p><span class="price">€ 13,50</span></div>
    <div class="menu-item"><h4>Carpaccio di Tonno</h4><p>Raw tuna with citrus and capers</p><span class="price">€ 14,50</span></div>
    <div class="menu-item"><h4>Vitello Tonnato</h4><p>Veal slices with creamy tuna sauce</p><span class="price">€ 14,75</span></div>
    <div class="menu-item"><h4>Antipasto Italiano</h4><p>Selection of cured meats and cheeses</p><span class="price">€ 16,00</span></div>
  </div>
</section>

<section class="testimonials">
  <div class="avatar" role="img" aria-label="Guest portrait" style="left:96px;top:100px;width:60px;height:60px;background:#d8ccbd"></div>
  <div class="arrow" style="left:200px;top:116px"><svg width="26" height="26" viewBox="0 0 26 26"><path d="M15 8 L10 13 L15 18" fill="none" stroke="#777" stroke-width="2"/></svg></div>
  <div class="avatar" role="img" aria-label="Guest portrait" style="left:284px;top:88px;width:80px;height:80px;background:#c9b29a;border:3px solid #fff"></div>
  <div class="quote">
    <h5>Lorem ipsum dolor sit amet, consectetur adipiscing elit.</h5>
    <p>Sed do eiusmod tempor incididunt ut labore et dolore magna aliqua. Ut enim ad minim veniam, quis nostrud exercitation.</p>
    <div class="author">Anna Visser <i></i></div>
  </div>
  <div class="arrow" style="left:970px;top:116px"><svg width="26" height="26" viewBox="0 0 26 26"><path d="M11 8 L16 13 L11 18" fill="none" stroke="#777" stroke-width="2"/></svg></div>
  <div class="avatar" role="img" aria-label="Guest portrait" style="left:1036px;top:100px;width:60px;height:60px;background:#d8ccbd"></div>
  <div class="abs" style="left:470px;top:226px;width:260px;height:3px;background:#ddd"><div style="width:80px;height:3px;background:var(--gold)"></div></div>
</section>

<h2 class="contact-title">Contact Us</h2>
<div class="form-field" style="top:2590px;height:30px">Name</div>
<div class="form-field" style="top:2628px;height:30px">Email</div>
<div class="form-field" style="top:2666px;height:92px">Message</div>
<div class="btn-gold" style="left:540px;top:2766px;width:60px;height:24px;line-height:24px">Send</div>

<div class="social-widget">
  <div class="widget-photo" role="img" aria-label="Restaurant team standing together"></div>
  <div class="widget-body">
    <strong>Teatro Lucerna</strong>
    <span>Italian restaurant · Amsterdam</span>
    <div class="widget-lines"><i style="width:90%"></i><i style="width:70%"></i><i style="width:80%"></i></div>
  </div>
</div>

<footer class="site-footer">
  <div class="foot-brand">
    <div class="name"><i></i>Teatro Lucerna</div>
    <div class="sub">Ristorante italiano</div>
    <address>Lucernastraat 7, 1099 ZZ Amsterdam<br>Phone: +31 20 555 0184</address>
  </div>
  <div class="foot-social"><i></i><i></i><i></i></div>
  <div class="foot-nav"><span>Home</span><span>Menu</span><span>Group Menu</span><span>Reservation</span><span>Blog</span><span>Contact</span></div>
  <div class="copyright">Copyright Teatro Lucerna 2024 – All Rights Reserved</div>
</footer>

</body>
</html>
```